Visitenkarten/Briefpaier/Kassenkassenbelege für Juwelier
Zielgruppe
Mittelständischer Juwelier mit zwei Filialen. Klassischer Schmuck, Uhren und Modeschmuck
Aufgabenstellung
Es müssen für zwei Geschäfte Visitenkarten, Briefpapier (A4) und Kassenkassenbelege (A6) erstellt werden. Logo und Typo im Anhang. Ein Farbkonzept besteht noch nicht. Die Idee geht in Richtung Bordeaux-Rot.
Generell:
(1) Sieht erstmal nach viel Beschreibung aus, bitte nicht entmutigen lassen, sind zu 90% nur austauschbare Inhalts-/Kontaktdaten.
(2) Für meine Zwecke reicht es vollkommen aus, wenn bei den Vorschlägen zur Arbeitsersparnis erstmal nur mit einer Adresse gearbeitet wird. Wenn ich dann den zutreffenden Designvorschlag gefunden habe, können wir die zweite Adresse in dem ersten Format umsetzen. Ich denke das spart Zeit und Nerven.
(3) Bitte Angaben wie "Tel.:" oder "USt.- ID:" nicht wörtlich nehmen, es soll dabei klar sein worum es geht; wenn "Telefon" ausgeschrieben besser aussieht, bitte in der optisch ansprechenderen Form verwenden.
(4) Bei Fragen, bitte fragen!
(5) Viel Spass bei dem Projekt - Ich freu' mich auf die Vorschläge!
Visitenkarten(1):
Juwelier Brenneck GmbH
www.juwelier-brenneck-beispiel.de
Visitenkarten(2):
Visitenkarten(generell):
(1) Die einzelnen Daten können durch Hervorhebungen wie Adresse, Kontakt, Online/Internet unterteilt bzw. hervorgehoben werden.
(2) Die Visitenkarten sollen farbig gedruckt werden; geplant ist weiß als Hintergrund ist aber nicht zwingend bei einer guten anderen Idee
Briefpapier:
(1)Absender im Adressfeld für DIN-lang Briefumschläge mit Fenster:
(2)Informationen im Footer/Seitenbereich:
Juwelier Brenneck Gmb..

```html
<!DOCTYPE html>
<html lang="de">
<head>
<meta charset="utf-8">
<title>Briefpapier Haus Brenneck</title>
<link rel="stylesheet" href="https://fonts.googleapis.com/css2?family=Source+Sans+3:wght@400;600&display=swap">
<style>
  :root {
    --page-bg: #ffffff;
    --canvas-bg: #ffffff;
    --accent-green: #6a9e80;
    --accent-blue: #2d5384;
    --accent-grey: #666666;
    --text-grey: #7a7a7a;
    --text-dark: #5a5a5a;
    --rule: #8a8a8a;
    --mark: #999999;
  }
  * { margin: 0; padding: 0; box-sizing: border-box; }
  html, body {
    width: 1200px; height: 814px; overflow: hidden;
    background: var(--canvas-bg);
    font-family: "Source Sans 3", "Source Sans Pro", sans-serif;
  }
  .canvas { position: relative; width: 1200px; height: 814px; }

  .crop { position: absolute; background: #777; }
  .crop.v { width: 1px; height: 30px; }
  .crop.h { height: 1px; width: 30px; }

  .sheet {
    position: absolute; top: 50px; width: 503px; height: 711px;
    background: var(--page-bg);
    box-shadow: 2px 3px 5px rgba(0,0,0,0.28);
  }
  .sheet--one { left: 50px; }
  .sheet--two { left: 646px; }

  .brand {
    position: absolute; display: flex; align-items: center; gap: 7px;
    white-space: nowrap;
  }
  .sheet--one .brand { left: 86px; top: 66px; }
  .sheet--two .brand { left: 30px; top: 40px; }
  .brand-square { width: 10px; height: 10px; }
  .sheet--one .brand-square { background: var(--accent-green); }
  .sheet--two .brand-square { background: var(--accent-grey); }
  .brand-name { font-size: 17px; font-weight: 400; color: var(--text-dark); }

  .window-mark { position: absolute; width: 11px; height: 11px; border-color: var(--mark); border-style: solid; border-width: 0; }
  .window-mark.tl { border-top-width: 1px; border-left-width: 1px; }
  .window-mark.tr { border-top-width: 1px; border-right-width: 1px; }
  .window-mark.bl { border-bottom-width: 1px; border-left-width: 1px; }
  .window-mark.br { border-bottom-width: 1px; border-right-width: 1px; }

  .fold-mark { position: absolute; left: 0; width: 17px; height: 1px; background: #bbb; }

  .info-rule { position: absolute; left: 367px; top: 0; width: 1px; height: 241px; background: var(--rule); }
  .sender-info { position: absolute; left: 377px; top: 39px; color: var(--text-grey); }
  .sender-info .company { font-size: 8.6px; font-weight: 600; color: var(--text-dark); margin-bottom: 1px; }
  .sender-info .line { font-size: 6.6px; line-height: 10.2px; }
  .sender-info .block { margin-top: 10px; }
  .sender-info .small { font-size: 5.4px; line-height: 7.7px; color: var(--text-dark); }
  .sender-info .small-block { margin-top: 12px; }
  .sender-info .small-block.tight { margin-top: 10px; }
  .sender-info .branch { font-size: 6.6px; line-height: 7.7px; color: var(--text-dark); margin-top: 12px; }

  .footer-band { position: absolute; left: 0; bottom: 0; width: 100%; height: 5px; }
  .sheet--one .footer-band { background: var(--accent-blue); }
  .sheet--two .footer-band { background: var(--accent-green); }
</style>
</head>
<body>
<div class="canvas">
  <span class="crop v" style="left:50px;top:5px"></span>
  <span class="crop v" style="left:553px;top:5px"></span>
  <span class="crop v" style="left:646px;top:5px"></span>
  <span class="crop v" style="left:1148px;top:5px"></span>
  <span class="crop v" style="left:50px;top:778px"></span>
  <span class="crop v" style="left:553px;top:778px"></span>
  <span class="crop v" style="left:646px;top:778px"></span>
  <span class="crop v" style="left:1148px;top:778px"></span>
  <span class="crop h" style="left:5px;top:50px"></span>
  <span class="crop h" style="left:568px;top:50px"></span>
  <span class="crop h" style="left:600px;top:50px"></span>
  <span class="crop h" style="left:1164px;top:50px"></span>
  <span class="crop h" style="left:5px;top:761px"></span>
  <span class="crop h" style="left:568px;top:761px"></span>
  <span class="crop h" style="left:600px;top:761px"></span>
  <span class="crop h" style="left:1164px;top:761px"></span>

  <section class="sheet sheet--one">
    <div class="brand"><span class="brand-square"></span><span class="brand-name">Haus Brenneck</span></div>
    <span class="window-mark tl" style="left:24px;top:122px"></span>
    <span class="window-mark tr" style="left:228px;top:122px"></span>
    <span class="window-mark bl" style="left:24px;top:194px"></span>
    <span class="window-mark br" style="left:228px;top:194px"></span>
    <span class="fold-mark" style="top:252px"></span>
    <span class="fold-mark" style="top:490px"></span>
    <div class="info-rule"></div>
    <div class="sender-info">
      <div class="company">Juwelier Brenneck GmbH</div>
      <div class="line">Goldschmiedweg 14</div>
      <div class="line">45100 Musterstadt a.d. Ruhr</div>
      <div class="block">
        <div class="line">Tel.: 0200-123456</div>
        <div class="line">Fax: 0200-123457</div>
        <div class="line">info@juwelier-brenneck-beispiel.de</div>
        <div class="line">www.juwelier-brenneck-beispiel.de</div>
      </div>
      <div class="small-block">
        <div class="small">Bankverbindung:</div>
        <div class="small">Beispielbank AG Musterstadt</div>
        <div class="small">IBAN: DE00 1234 5678 9012 3456 78</div>
        <div class="small">BIC: BSPL DE 1X</div>
      </div>
      <div class="small-block tight">
        <div class="small">Steuernummer:</div>
        <div class="small">100/1000/0000</div>
        <div class="small">USt.- ID: DE 000000000</div>
      </div>
      <div class="branch">Filiale:<br>Lindenallee 8<br>45200 Beispielheim</div>
    </div>
    <div class="footer-band"></div>
  </section>

  <section class="sheet sheet--two">
    <div class="brand"><span class="brand-square"></span><span class="brand-name">Haus Brenneck</span></div>
    <span class="window-mark tl" style="left:24px;top:122px"></span>
    <span class="window-mark tr" style="left:228px;top:122px"></span>
    <span class="window-mark bl" style="left:24px;top:194px"></span>
    <span class="window-mark br" style="left:228px;top:194px"></span>
    <span class="fold-mark" style="top:252px"></span>
    <span class="fold-mark" style="top:490px"></span>
    <div class="info-rule"></div>
    <div class="sender-info">
      <div class="company">Juwelier Brenneck GmbH</div>
      <div class="line">Goldschmiedweg 14</div>
      <div class="line">45100 Musterstadt a.d. Ruhr</div>
      <div class="block">
        <div class="line">Tel.: 0200-123456</div>
        <div class="line">Fax: 0200-123457</div>
        <div class="line">info@juwelier-brenneck-beispiel.de</div>
        <div class="line">www.juwelier-brenneck-beispiel.de</div>
      </div>
      <div class="small-block">
        <div class="small">Bankverbindung:</div>
        <div class="small">Beispielbank AG Musterstadt</div>
        <div class="small">IBAN: DE00 1234 5678 9012 3456 78</div>
        <div class="small">BIC: BSPL DE 1X</div>
      </div>
      <div class="small-block tight">
        <div class="small">Steuernummer:</div>
        <div class="small">100/1000/0000</div>
        <div class="small">USt.- ID: DE 000000000</div>
      </div>
      <div class="branch">Filiale:<br>Lindenallee 8<br>45200 Beispielheim</div>
    </div>
    <div class="footer-band"></div>
  </section>
</div>
</body>
</html>
```